Corwin Beacon Lighting - Commercial & Residential Landscape Lighting

Landscape Lighting Services & Design: Create a website for our landscape lighting company. We would like the design to be tailored around this description:
Illuminate with Confidence. Designed with Precision. Installed with Care.
Locally and veteran-owned, we take pride in transforming outdoor spaces through innovative lighting solutions tailored to your vision. From landscape and holiday lighting to permanent installations, our effortless process and expert design deliver breathtaking results and lasting curb appeal. Backed by a lifetime warranty and quarterly service options, our commitment to quality and customer satisfaction is unwavering. Try before you buy and experience your home in a whole new light with our complimentary demo kit — see the stunning effects before you decide.
- Also, add in this information as well; Outdoor Lighting not only beautifies spaces but also significantly enhances safety by illuminating your home or business. Beautifully lit entrances deter potential intruders, making your home a safer place for your loved ones. we also offer quarterly service plans to ensure lighting equipment continues to operate & illuminate effectively throughout the year. Also mention we provide free estimates and we are offering a 10% discount to military, veterans, and first responders.

Target Market(s)

Luxury market

Industry/Entity Type

Landscape Lighting - Residential & Commercial Lighting Services

Coding

Coded - Design and coding required

Number of Pages Required

2 page

Colors
00AB8E
00BBA5
67D7C9
C6EFE9
E9F9F6
59FF00
82FF00
B8FF75
E3FFCB
F4FFEA
FFC000
F8CF3A
FAE287
FDF2CF
FEFAEE

Requirements
Must have
• a lead generation button where people can submit their information for us to reach out to them and schedule their free estimate, homepage, about page, contact page, products and services page, user friendly, easy to navigate, and it also must be engaging and eye popping, as well as appealing to the luxury market. Please use colors; verdent green, dark green, ivory, and sunny yellow. Also, include an about page that references our story; Derek is retired Army and he opened a fitness studio in 2017 with his wife Jolene. He has installed low voltage lighting in every home he lived in and for his friends and family over the years and decided to open his own business because he is passionate about beautifying outdoor landscapes and highlighting a properties full potential, not only in the day but at night as well all while providing safety and security for his clients. Having a deep respect for nature and landscaping, he wants to provide the same care and quality to each of his clients as he has in the fitness industry for decades. He believes small businesses are the back bone of America and he's excited to provide a service that is all to often neglected in the design of a home.
Nice to have
• I would like to have a clear intent and purpose, engaging web design, clear call to action, optimized for search engines, mobile friendy design, security measures, credibility indicators

```html
<!DOCTYPE html>
<html lang="en">
<head>
<meta charset="utf-8">
<title>Corwin Beacon Lighting – Residential &amp; Commercial Landscape Lighting</title>
<link href="https://fonts.googleapis.com/css2?family=Lexend:wght@400;500&family=Montserrat:wght@400;500;600;700&display=swap" rel="stylesheet">
<style>
:root{
  --gold:#F8CF3A;
  --gold-deep:#E9A93A;
  --amber:#FFC000;
  --teal:#00AB8E;
  --teal-light:#00BBA5;
  --forest:#0E4A33;
  --forest-deep:#0A3325;
  --ivory:#FEFAEE;
  --black:#000;
  --ink:#111;
  --text:#EDE6D6;
}
*{margin:0;padding:0;box-sizing:border-box}
html,body{width:1200px;height:4418px;overflow:hidden;background:var(--black)}
body{font-family:"Montserrat",sans-serif;color:var(--text);position:relative}
.head{font-family:"Lexend",sans-serif;font-weight:400;text-transform:uppercase}
.gold-text{color:var(--gold-deep)}
.btn{display:inline-flex;align-items:center;justify-content:center;border-radius:30px;font-weight:700;font-size:13px;letter-spacing:.5px;text-transform:uppercase;text-decoration:none}
.btn-gold{background:linear-gradient(90deg,var(--amber),var(--gold-deep));color:#1a1200}
.btn-teal{background:linear-gradient(90deg,var(--teal),var(--teal-light));color:#fff}
.btn-outline-light{border:2px solid #fff;color:#fff}
.btn-outline-dark{border:2px solid #1a1200;color:#1a1200}
.abs{position:absolute}
.photo{position:absolute}

/* nav */
.nav{position:absolute;top:0;left:0;width:1200px;height:104px;z-index:5}
.nav a{position:absolute;top:60px;color:var(--gold);font-size:14px;text-decoration:none;text-transform:uppercase;letter-spacing:.5px}
.nav .active{border-bottom:2px solid var(--gold);padding-bottom:14px}
.nav .rule{position:absolute;top:103px;left:120px;width:960px;height:1px;background:rgba(248,207,58,.25)}
.brand{position:absolute;left:480px;top:28px;width:240px;text-align:center;color:var(--gold-deep);font-family:"Lexend",sans-serif;font-weight:400;font-size:24px;line-height:30px;text-transform:uppercase;letter-spacing:2px}
.nav .btn{position:absolute;left:1016px;top:48px;width:154px;height:38px;font-size:12px}

/* hero */
.hero{top:0;left:0;width:1200px;height:740px;background:
  radial-gradient(ellipse at 20% 55%,rgba(214,136,60,.55),transparent 45%),
  radial-gradient(ellipse at 85% 50%,rgba(214,136,60,.5),transparent 40%),
  linear-gradient(180deg,#2b3340 0%,#3a4240 40%,#3d4a2c 70%,#2d3a1f 100%)}
.hero-title{position:absolute;top:202px;left:0;width:1200px;text-align:center;font-size:40px;line-height:50px;letter-spacing:1px;color:var(--gold)}
.hero-rule{position:absolute;top:362px;left:440px;width:320px;height:2px;background:linear-gradient(90deg,transparent,var(--gold),transparent)}
.hero .btn{position:absolute;top:392px;left:510px;width:180px;height:42px}
.hero-curve{position:absolute;top:600px;left:0}

/* about */
.about-photo{left:190px;top:848px;width:396px;height:414px;border-radius:50%;border:3px solid var(--gold-deep);background:radial-gradient(circle at 50% 40%,#8a6a3a,#4a5a2a 55%,#a08428 100%)}
.eyebrow{font-size:14px;letter-spacing:4px;text-transform:uppercase;color:var(--text)}
.about-eyebrow{left:618px;top:782px}
.about-title{left:614px;top:800px;font-size:38px;line-height:46px;color:var(--ivory)}
.title-rule{height:4px;width:140px;background:linear-gradient(90deg,var(--gold-deep),transparent)}
.about-rule{left:616px;top:898px}
.about-copy{left:616px;top:922px;width:528px;font-size:15.5px;line-height:27px;color:#e8e2d4}
.about-quote{left:620px;top:1124px;width:500px;padding-left:14px;border-left:2px solid var(--gold-deep);font-size:15.5px;line-height:27px;font-weight:700;color:var(--ivory)}
.about-btn{left:620px;top:1236px;width:180px;height:42px}
.offer{top:1332px;width:466px;height:139px;display:flex;align-items:center;padding-left:34px;gap:20px;background:#050505}
.offer-teal{left:121px;border:2px solid #1b5a3c}
.offer-gold{left:612px;border:2px solid #6a5420}
.offer-icon{width:76px;height:76px;border-radius:50%;flex:none;display:flex;align-items:center;justify-content:center}
.offer-teal .offer-icon{background:var(--teal)}
.offer-gold .offer-icon{background:var(--amber)}
.offer h3{font-family:"Lexend",sans-serif;font-weight:400;font-size:20px;text-transform:uppercase;color:var(--ivory);letter-spacing:.5px}
.offer p{font-size:16px;text-transform:uppercase;color:#ddd;line-height:21px;margin-top:4px}

/* split */
.split{top:1563px;width:600px;height:464px;text-align:center}
.split-res{left:0;background:linear-gradient(135deg,#1a7d5c 0%,#0f9f7e 50%,#1d9a74 100%)}
.split-com{left:600px;background:linear-gradient(135deg,#f2a72e 0%,#f8c23e 55%,#f3a841 100%)}
.split h2{margin-top:122px;font-size:32px;line-height:40px;letter-spacing:1px}
.split p{margin:28px auto 0;width:440px;font-size:16.5px;line-height:27px}
.split .btn{margin-top:24px;width:180px;height:44px}
.split-res h2,.split-res p{color:#fff}
.split-com h2,.split-com p{color:#1a1200}

/* products */
.products{top:2027px;left:0;width:1200px;height:716px;background:
  radial-gradient(ellipse at 75% 75%,rgba(200,130,40,.55),transparent 45%),
  radial-gradient(ellipse at 15% 60%,rgba(60,90,40,.5),transparent 45%),
  linear-gradient(180deg,#050505 0%,#141410 40%,#2a1f12 80%,#060606 100%)}
.prod-eyebrow{top:2113px;left:0;width:1200px;text-align:center}
.prod-title{top:2130px;left:0;width:1200px;text-align:center;font-size:38px;color:var(--gold-deep)}
.prod-rule{top:2186px;left:470px;width:260px;height:3px;background:linear-gradient(90deg,transparent,var(--gold-deep),transparent)}
.circle{border-radius:50%;text-align:center;overflow:hidden}
.circle .label{position:absolute;left:0;width:100%;font-family:"Lexend",sans-serif;font-weight:500;font-size:22px;line-height:29px;text-transform:uppercase}
.c-land{left:84px;top:2255px;width:330px;height:330px;background:linear-gradient(180deg,#2f4a20,#4d6a24 50%,#2a2f18)}
.c-land .label{top:228px;color:var(--gold)}
.c-land .label span{color:#fff}
.c-holi{left:435px;top:2248px;width:340px;height:340px;border:2px solid var(--gold-deep);background:radial-gradient(circle,#1e5a3c,#123f2b)}
.c-holi .label{top:88px;color:var(--gold)}
.c-holi .label span{color:#fff}
.c-holi p{position:absolute;top:160px;left:60px;width:220px;font-size:12px;line-height:19px;color:#e8e8e0}
.c-holi .btn{position:absolute;top:254px;left:108px;width:124px;height:32px;font-size:11px}
.c-perm{left:797px;top:2260px;width:330px;height:330px;background:linear-gradient(180deg,#203a6a,#4a4a5a 45%,#9a6a2a 80%,#3a2a1a)}
.c-perm .label{top:228px;color:var(--gold)}
.c-perm .label span{color:#fff}

/* why */
.why-eyebrow{left:137px;top:2820px}
.why-title{left:134px;top:2840px;font-size:38px;line-height:46px;color:var(--gold-deep)}
.why-rule{left:134px;top:2940px}
.why-copy{left:132px;top:2978px;width:496px;font-size:18px;line-height:27px;color:#e6dfd0}
.why-copy p+p{margin-top:27px;width:410px}
.why-btn{left:140px;top:3273px;width:180px;height:44px}
.why-big{left:663px;top:2823px;width:478px;height:448px;border-radius:10px;background:linear-gradient(180deg,#1a2430 0%,#5a4a44 35%,#8a5a3a 55%,#4a5a2a 80%,#3a4a22 100%)}
.why-small{left:576px;top:3120px;width:316px;height:252px;border-radius:8px;border:2px solid #111;background:linear-gradient(180deg,#2a4a7a 0%,#8a7a6a 45%,#c69a5a 65%,#5a5a50 100%)}

/* contact */
.contact-bg{top:3480px;left:0;width:1200px;height:670px;background:
  radial-gradient(ellipse at 7% 42%,rgba(255,200,90,.55),transparent 14%),
  linear-gradient(180deg,#071810 0%,#13301f 45%,#1e2a18 75%,#0a0a06 100%)}
.contact-card{left:132px;top:3535px;width:945px;height:560px;border-radius:18px;border:2px solid #2f6a44;background:rgba(14,74,51,.93)}
.contact-eyebrow{top:3612px;left:132px;width:945px;text-align:center;color:var(--gold-deep)}
.contact-title{top:3630px;left:132px;width:945px;text-align:center;font-size:34px;color:var(--gold)}
.contact-rule{top:3680px;left:500px;width:210px;height:3px;background:linear-gradient(90deg,transparent,var(--gold-deep),transparent)}
.field{height:48px;background:rgba(0,0,0,.55);border:1px solid #4b6a4c;display:flex;align-items:center;gap:8px;padding-left:18px;font-size:14px;color:#e6e6e6}
.f1{left:234px;top:3716px;width:360px}
.f2{left:605px;top:3716px;width:360px}
.f3{left:234px;top:3778px;width:360px}
.f4{left:605px;top:3778px;width:360px}
.f5{left:234px;top:3840px;width:731px;height:118px;align-items:flex-start;padding-top:18px}
.send{left:494px;top:3981px;width:210px;height:48px;font-size:15px}

/* footer */
.footer-rule{top:4152px;left:132px;width:945px;height:1px;background:#333}
.fnav a{position:absolute;top:4190px;color:#fff;font-size:13px;font-weight:700;text-transform:uppercase;text-decoration:none}
.fnav .dot{position:absolute;top:4195px;width:4px;height:4px;border-radius:50%;background:var(--gold-deep)}
.fbrand{left:500px;top:4168px;width:220px;text-align:center;color:var(--gold-deep);font-family:"Lexend",sans-serif;font-size:24px;line-height:30px;text-transform:uppercase;letter-spacing:2px}
.finfo{top:4278px;display:flex;align-items:center;gap:14px;font-size:13px;font-weight:600;color:#fff}
.finfo .ic{width:36px;height:36px;border-radius:50%;background:var(--amber);display:flex;align-items:center;justify-content:center}
.social{top:4290px;left:934px;display:flex;gap:13px}
.social span{width:26px;height:26px;border-radius:50%;background:var(--gold-deep);display:block}
.copyright{top:4363px;left:0;width:1200px;height:55px;background:#1b1b1b;text-align:center;line-height:55px;font-size:13px;color:#cfcfcf}
</style>
</head>
<body>

<!-- hero -->
<section class="photo hero" role="img" aria-label="Night view of a brick house with warm landscape lighting along the lawn and walkway">
  <h1 class="head hero-title">Illuminate with confidence.<br>Designed with precision.<br>Installed with care.</h1>
  <div class="hero-rule"></div>
  <a class="btn btn-teal" href="#estimate">Free Estimate &rsaquo;</a>
  <svg class="hero-curve" width="1200" height="142" viewBox="0 0 1200 142">
    <path d="M0 142 L0 40 Q300 0 600 28 Q900 0 1200 40 L1200 142 Z" fill="#000"/>
    <path d="M0 40 Q300 0 600 28 Q900 0 1200 40" fill="none" stroke="#E9A93A" stroke-width="2"/>
  </svg>
</section>

<nav class="nav">
  <a class="active" style="left:140px" href="#">Home</a>
  <a style="left:234px" href="#">About</a>
  <a style="left:336px" href="#">Services</a>
  <div class="brand">Corwin Beacon Lighting</div>
  <a style="left:750px" href="#">Products</a>
  <a style="left:882px" href="#">Contact Us</a>
  <a class="btn btn-gold" href="#estimate">Free Estimate &rsaquo;</a>
  <div class="rule"></div>
</nav>

<!-- about -->
<div class="photo about-photo" role="img" aria-label="Brick home on a wide lawn at dusk with warm uplighting"></div>
<p class="abs eyebrow about-eyebrow">Who we are</p>
<h2 class="abs head about-title">About Corwin Beacon<br>Lighting</h2>
<div class="abs title-rule about-rule"></div>
<p class="abs about-copy">Locally and veteran-owned, we take pride in transforming outdoor spaces through innovative lighting solutions tailored to your vision. From landscape and holiday lighting to permanent installations, our effortless process and expert design deliver breathtaking results and lasting curb appeal. Backed by a lifetime warranty and quarterly service options, our commitment to quality and customer satisfaction is unwavering.</p>
<p class="abs about-quote">Try before you buy and experience your home in a whole new light with our complimentary demo kit — see the stunning effects before you decide.</p>
<a class="abs btn btn-gold about-btn" href="#">Learn More &rsaquo;</a>

<div class="abs offer offer-teal">
  <div class="offer-icon">
    <svg width="40" height="40" viewBox="0 0 40 40" fill="none" stroke="#fff" stroke-width="2"><rect x="9" y="6" width="22" height="28" rx="2"/><path d="M14 14h12M14 20h12M14 26h8"/></svg>
  </div>
  <div><h3>We provide free estimate</h3><p>Get a free estimate now</p></div>
</div>
<div class="abs offer offer-gold">
  <div class="offer-icon">
    <svg width="40" height="40" viewBox="0 0 40 40" fill="none" stroke="#1a1200" stroke-width="2"><circle cx="20" cy="24" r="9"/><path d="M14 5l6 10 6-10"/></svg>
  </div>
  <div><h3>We offering a 10% discount</h3><p>To military, veterans, and<br>first responders</p></div>
</div>

<!-- residential / commercial -->
<section class="abs split split-res" role="img" aria-label="Garden steps with landscape lights under a green tint">
  <h2 class="head">Residential<br>Landscape Lighting</h2>
  <p>Lorem ipsum dolor sit amet, consectetur adipiscing elit, sed do eiusmod tempor incididun</p>
  <a class="btn btn-outline-light" href="#">Learn More &rsaquo;</a>
</section>
<section class="abs split split-com" role="img" aria-label="Commercial grounds with lighting under a warm yellow tint">
  <h2 class="head">Commercial<br>Landscape Lighting</h2>
  <p>Lorem ipsum dolor sit amet, consectetur adipiscing elit, sed do eiusmod tempor incididun</p>
  <a class="btn btn-outline-dark" href="#">Learn More &rsaquo;</a>
</section>

<!-- products & services -->
<section class="photo products" role="img" aria-label="Lit patio and garden at night"></section>
<p class="abs eyebrow prod-eyebrow">What we do</p>
<h2 class="abs head prod-title">Products &amp; Services</h2>
<div class="abs prod-rule"></div>

<div class="abs circle c-land" role="img" aria-label="Garden beds with path lights">
  <div class="label">Landscape<br><span>Lighting</span></div>
</div>
<div class="abs circle c-holi">
  <div class="label">Holiday<br><span>Lighting</span></div>
  <p>Lorem ipsum dolor sit amet, consectetur adipiscing elit, sed do eiusmod tempor incididunt ut labore et dolore magna aliqua.</p>
  <a class="btn btn-gold" href="#">Learn More &rsaquo;</a>
</div>
<div class="abs circle c-perm" role="img" aria-label="Large home with permanent facade lighting at dusk">
  <div class="label">Permanent<br><span>Installations</span></div>
</div>

<!-- why outdoor lighting -->
<p class="abs eyebrow why-eyebrow">Outdoor lighting</p>
<h2 class="abs head why-title">Why outdoor<br>lighting</h2>
<div class="abs title-rule why-rule"></div>
<div class="abs why-copy">
  <p>Outdoor Lighting not only beautifies spaces but also significantly enhances safety by illuminating your home or business.</p>
  <p>Beautifully lit entrances deter potential intruders, making your home a safer place for your loved ones. we also offer quarterly service plans to ensure lighting equipment continues to operate &amp; illuminate effectively throughout the year.</p>
</div>
<a class="abs btn btn-gold why-btn" href="#estimate">Free Estimate &rsaquo;</a>
<div class="photo why-big" role="img" aria-label="Brick home with lit shrubs and lawn at twilight"></div>
<div class="photo why-small" role="img" aria-label="Modern home with glowing walls and lit tree at dusk"></div>

<!-- contact -->
<section class="photo contact-bg" role="img" aria-label="Garden with glowing bollard light at night"></section>
<div class="abs contact-card" id="estimate"></div>
<p class="abs eyebrow contact-eyebrow">Contact us</p>
<h2 class="abs head contact-title">Schedule free estimate</h2>
<div class="abs contact-rule"></div>

<div class="abs field f1"><svg width="12" height="12" viewBox="0 0 12 12" fill="#ccc"><circle cx="6" cy="3.5" r="3"/><path d="M0 12a6 5 0 0 1 12 0z"/></svg>First Name</div>
<div class="abs field f2"><svg width="12" height="12" viewBox="0 0 12 12" fill="#ccc"><circle cx="6" cy="3.5" r="3"/><path d="M0 12a6 5 0 0 1 12 0z"/></svg>Last Name</div>
<div class="abs field f3"><svg width="13" height="10" viewBox="0 0 13 10" fill="#ccc"><rect width="13" height="10" rx="1"/><path d="M0 1l6.5 5L13 1" stroke="#333" fill="none"/></svg>Email address</div>
<div class="abs field f4"><svg width="12" height="12" viewBox="0 0 12 12" fill="#ccc"><path d="M2 0l3 3-1.5 1.5a8 8 0 0 0 4 4L9 7l3 3-2 2C5 12 0 7 0 2z"/></svg>Phone number</div>
<div class="abs field f5"><svg width="13" height="11" viewBox="0 0 13 11" fill="#ccc"><ellipse cx="6.5" cy="4.5" rx="6.5" ry="4.5"/><path d="M2 7l-1 4 4-2z"/></svg>Leave Message</div>
<a class="abs btn btn-gold send" href="#">Send Message &rsaquo;</a>

<!-- footer -->
<div class="abs footer-rule"></div>
<nav class="fnav">
  <a style="left:142px" href="#">Home</a><span class="dot" style="left:226px"></span>
  <a style="left:256px" href="#">About Us</a><span class="dot" style="left:366px"></span>
  <a style="left:398px" href="#">Services</a>
  <a style="left:736px" href="#">Products</a><span class="dot" style="left:848px"></span>
  <a style="left:885px" href="#">Gallery</a><span class="dot" style="left:982px"></span>
  <a style="left:1016px" href="#">Contact</a>
</nav>
<div class="abs fbrand">Corwin Beacon Lighting</div>

<div class="abs finfo" style="left:130px"><span class="ic"><svg width="14" height="18" viewBox="0 0 14 18" fill="#fff"><path d="M7 0a7 7 0 0 1 7 7c0 5-7 11-7 11S0 12 0 7a7 7 0 0 1 7-7z"/><circle cx="7" cy="7" r="2.5" fill="#FFC000"/></svg></span>123 Street Address line</div>
<div class="abs finfo" style="left:412px"><span class="ic"><svg width="16" height="16" viewBox="0 0 12 12" fill="#fff"><path d="M2 0l3 3-1.5 1.5a8 8 0 0 0 4 4L9 7l3 3-2 2C5 12 0 7 0 2z"/></svg></span>(555) 014-2287</div>
<div class="abs finfo" style="left:614px"><span class="ic"><svg width="16" height="12" viewBox="0 0 13 10" fill="#fff"><rect width="13" height="10" rx="1"/><path d="M0 1l6.5 5L13 1" stroke="#FFC000" fill="none"/></svg></span>enquiry@corwinbeacon.com</div>
<div class="abs social" aria-label="Social links"><span></span><span></span><span></span><span></span></div>

<div class="abs copyright">Copyright © 2025 Corwin Beacon &nbsp;|&nbsp; All Right Reserved</div>

</body>
</html>
```